Willow Cradle Pregnancy and Baby Massage

I need a web design for a new business, WILLOW CRADLE PREGNANCY AND BABY MASSAGE that I am in the process of setting up in the suburbs of Perth, Western Australia. The business is owned and operated by myself and my intention is to service Pregnant Mothers and Parents of Young Babies that would benefit from massage. I would like to have a "Home Page" and pages for "About Me", "Pregnancy Massage", "Baby Massage", a Pricing Page for Pregnancy Massage Sessions, a Pricing Page for Baby Massage Sessions, and a "Contact Me" page to allow clients to either contact me with queries or book available pregnancy massage sessions on a particular day of the week. I would also like a "News" page that would include articles I have written, news about new courses and a link to my Facebook page (yet to be set up). I would like to keep the colour schemes similar to my logo design colours. I need the design to be easy to follow and to appeal to a younger audience (20's to mid 30's).
The target audience is pregnant mothers-to-be wishing to receive massage treatments, and new parents and grandparents of small babies that would like to learn how to massage their babies.
The look and feel should be modern, professional, elegant and feminine.
I need the design to be in a standard format such that I can update the content by myself ( and does not need specialised software) as the company and business progresses.

Target Market(s)

Contact Information for Business Card

Card should have rounded edges. Design should have the same "feel" as the website. Contact Details of my business address, mobile phone, email and website should be included.

Font styles to use
Script

Requirements
Must have
• Same colours as logo design. In cmyk system, the colours are: 20,60,0,0 which best result is pantone 681 and 40,40,0,0 which best result is pantone 2645. Card should include the logo design.

```html
<!DOCTYPE html>
<html lang="en">
<head>
<meta charset="utf-8">
<title>Willow Cradle Pregnancy and Baby Massage</title>
<link href="https://fonts.googleapis.com/css2?family=Roboto:wght@300;400&family=Roboto+Slab:wght@400&display=swap" rel="stylesheet">
<style>
  :root {
    --orchid: #b565a7;
    --orchid-line: #c77bb5;
    --lavender: #a19ac8;
    --ink: #222;
    --body: #333;
    --grey: #8a8a8a;
    --white: #fff;
  }
  * { margin: 0; padding: 0; box-sizing: border-box; }
  html, body { width: 954px; height: 1200px; overflow: hidden; }
  body { font-family: 'Roboto', sans-serif; background: var(--white); color: var(--body); position: relative; }

  .top-rule { position: absolute; left: 0; top: 0; width: 954px; height: 3px; background: var(--orchid-line); }

  .site-header { position: absolute; left: 0; top: 3px; width: 954px; height: 99px; }
  .brand { position: absolute; left: 78px; top: 24px; display: flex; align-items: center; gap: 8px; color: var(--orchid); font-weight: 400; }
  .brand-dot { width: 22px; height: 22px; border-radius: 50%; background: var(--orchid); flex: none; }
  .brand-name { font-size: 15px; line-height: 18px; }
  .brand-name span { display: block; font-size: 10.5px; line-height: 14px; }

  .main-nav { position: absolute; right: 79px; top: 46px; display: flex; gap: 24px; font-size: 11px; }
  .main-nav a { color: var(--ink); text-decoration: none; }
  .main-nav a.current { color: var(--orchid); }

  .hero { position: absolute; left: 0; top: 102px; width: 954px; height: 474px;
    background: radial-gradient(ellipse at 62% 50%, #e0927b 0%, #b8786e 30%, #8c6a74 60%, #6f5a6a 100%); }
  .hero-title { position: absolute; left: 78px; top: 190px; font-family: 'Roboto Slab', serif; font-size: 26px; line-height: 32px; color: var(--white); font-weight: 400; }
  .hero-text { position: absolute; left: 78px; top: 272px; width: 400px; font-size: 16px; line-height: 24.6px; color: var(--white); font-weight: 300; }
  .hero-arrows { position: absolute; left: 76px; top: 384px; display: flex; gap: 10px; }

  .welcome-photo { position: absolute; left: 78px; top: 602px; width: 436px; height: 326px;
    background: radial-gradient(ellipse at 50% 55%, #d9a89c 0%, #9a7566 40%, #6d5446 70%, #c9ad8c 100%); }

  .welcome-card { position: absolute; left: 426px; top: 636px; width: 449px; height: 239px; background: var(--white);
    border-left: 5px solid var(--orchid); box-shadow: 0 2px 10px rgba(0,0,0,0.15); padding: 12px 29px 0 22px; }
  .welcome-card h2 { font-weight: 400; font-size: 22px; color: var(--orchid); margin-bottom: 5px; }
  .welcome-card p { font-size: 12px; line-height: 24.5px; text-align: justify; color: var(--body); }

  .certification { position: absolute; left: 596px; top: 910px; display: flex; gap: 14px; }
  .cert-badge { width: 116px; height: 144px; }
  .cert-text { font-weight: 300; font-size: 24px; line-height: 30px; color: var(--grey); }
  .cert-text em { font-style: normal; color: var(--orchid); }

  .site-footer { position: absolute; left: 0; top: 1075px; width: 954px; height: 125px; background: var(--lavender); color: var(--white); }
  .footer-nav { position: absolute; top: 25px; left: 0; width: 954px; display: flex; justify-content: center; gap: 24px; font-size: 11.5px; }
  .footer-nav a { color: var(--white); text-decoration: none; }
  .social { position: absolute; top: 50px; left: 399px; display: flex; gap: 10px; }
  .social a { width: 31px; height: 31px; border-radius: 50%; background: var(--white); display: block; }
  .copyright { position: absolute; top: 92px; left: 0; width: 954px; text-align: center; font-size: 9.5px; }
</style>
</head>
<body>
  <div class="top-rule"></div>

  <header class="site-header">
    <div class="brand">
      <div class="brand-dot"></div>
      <div class="brand-name">Willow Cradle<span>Pregnancy and Baby Massage</span></div>
    </div>
    <nav class="main-nav">
      <a class="current" href="#">Home</a>
      <a href="#">About Me</a>
      <a href="#">Pregnancy Massage</a>
      <a href="#">Baby Massage</a>
      <a href="#">Pricing</a>
      <a href="#">News</a>
      <a href="#">Contact Me</a>
    </nav>
  </header>

  <section class="hero" role="img" aria-label="Photo of two newborn twins sleeping wrapped in a coral blanket in a lace heart-shaped basket">
    <h1 class="hero-title">Willow Cradle Pregnancy<br>and Baby Massage</h1>
    <p class="hero-text">was launched in 2017, offering massage for pregnant women, and instruction of baby massage to parents, grandparents and carers.</p>
    <div class="hero-arrows">
      <svg width="14" height="16" viewBox="0 0 14 16"><path d="M10 2 L4 8 L10 14" fill="none" stroke="#fff" stroke-width="2"/></svg>
      <svg width="14" height="16" viewBox="0 0 14 16"><path d="M4 2 L10 8 L4 14" fill="none" stroke="#fff" stroke-width="2"/></svg>
    </div>
  </section>

  <div class="welcome-photo" role="img" aria-label="Photo of two newborn twins sleeping together in a fur-lined basket"></div>

  <article class="welcome-card">
    <h2>Welcome</h2>
    <p>My vision is to provide a professional massage service to pregnant mothers and babies that also benefitsfrom my skills and experience as a midwife.</p>
    <p>My expectation is that after each session, my clients should leave feeling relaxed, calm,emotionally nurtured, soothed and supported.</p>
    <p>At all times, I will take the utmost care of your privacy, safety and comfort in what is a very personal, intimate time in your life.</p>
  </article>

  <div class="certification">
    <svg class="cert-badge" viewBox="0 0 116 144" role="img" aria-label="Certification badge">
      <rect x="8" y="8" width="100" height="128" rx="6" fill="none" stroke="#b565a7" stroke-width="1.5"/>
    </svg>
    <div class="cert-text">Certified by<br><em>Little Touch</em><br><em>Infant Care</em><br>Network</div>
  </div>

  <footer class="site-footer">
    <nav class="footer-nav">
      <a href="#">Home</a>
      <a href="#">About Me</a>
      <a href="#">Pregnancy Massage</a>
      <a href="#">Baby Massage</a>
      <a href="#">Pricing</a>
      <a href="#">News</a>
      <a href="#">Contact Me</a>
    </nav>
    <div class="social">
      <a href="#" aria-label="Social profile 1"></a>
      <a href="#" aria-label="Social profile 2"></a>
      <a href="#" aria-label="Social profile 3"></a>
      <a href="#" aria-label="Social profile 4"></a>
    </div>
    <p class="copyright">© 2017. www.willowcradle.com.au &nbsp;|&nbsp; All rights reserved</p>
  </footer>
</body>
</html>
```